Bright Builders WA Gala Poster

To Create a Poster for the Bright Builders WA Gala 2013

Target Market(s)

Young Professional Engineers aged 18-35. Male and Female

Requirements
Must have
• All Details required for the ball. Black and white/silver theme. Some kind of engineering theme. Must have the following text:

Join us in celebrating the Annual Bright Builders of Western Australia Gala with a night of dinner and entertainment.
Saturday July 13th, 2013
Time: 7pm Arrival
Venue: Corvane Ridgeway Hotel, Perth
Dress: Formal
The evening will include drinks, a three-course dinner, music and dancing.
Ticket price $139, on sale now! To purchase tickets go to:
(website to be announced)
Proceeds go to Makers Across Oceans
is is an 18+ event. Open to general public.
Nice to have
• Modern, Classy, Similar to previous years designs. Possibly Masquerade themed.
Should not have
• Fish, environmental theme, rural Australia theme (these have been done)

```html
<!DOCTYPE html>
<html lang="en">
<head>
<meta charset="utf-8">
<title>Bright Builders WA Gala 2013</title>
<link rel="stylesheet" href="https://fonts.googleapis.com/css2?family=Cinzel:wght@400;500&family=EB+Garamond:ital,wght@0,500;0,600;1,500&display=swap">
<style>
  :root {
    --ink: #000000;
    --paper: #ffffff;
    --text-light: #f2f0ea;
    --gold: #b8955a;
    --gold-soft: #cdb07a;
    --gold-band: #a5824a;
    --grey-band: #4a4a4a;
    --logo-ink: #2b2b2b;
    --badge-green: #8fb84a;
    --mark-red: #e0321e;
    --heading-font: "Cinzel", "Times New Roman", serif;
    --body-font: "EB Garamond", Georgia, serif;
  }
  * { margin: 0; padding: 0; box-sizing: border-box; }
  html, body { width: 1200px; height: 2400px; overflow: hidden; background: var(--ink); }
  .poster { position: relative; width: 1200px; height: 2400px; background: var(--ink); overflow: hidden; }

  .hero-image {
    position: absolute; left: 0; top: 0; width: 1200px; height: 1000px;
    background:
      linear-gradient(180deg, rgba(0,0,0,0) 78%, rgba(0,0,0,1) 100%),
      radial-gradient(ellipse 300px 200px at 980px 300px, rgba(250,226,168,0.9), rgba(250,226,168,0) 100%),
      radial-gradient(ellipse 760px 560px at 860px 420px, rgba(226,194,120,0.95) 0%, rgba(176,138,72,0.85) 32%, rgba(104,76,34,0.65) 58%, rgba(30,22,10,0.3) 80%, rgba(0,0,0,0) 95%),
      linear-gradient(118deg, rgba(0,0,0,0) 25%, rgba(184,149,90,0.35) 55%, rgba(0,0,0,0) 88%),
      radial-gradient(ellipse 420px 620px at 250px 440px, rgba(80,80,80,0.6), rgba(0,0,0,0) 75%),
      linear-gradient(180deg, #0d0d0d 0%, #050505 100%);
  }

  .org-mark {
    position: absolute; left: 60px; top: 76px; width: 190px;
    display: flex; flex-direction: column; align-items: center; gap: 16px;
    font-family: var(--body-font); font-weight: 500; color: var(--text-light); text-align: center;
  }
  .org-mark .mark-square { width: 90px; height: 90px; background: var(--mark-red); }
  .org-mark .mark-name { font-size: 20px; line-height: 1.25; letter-spacing: 1px; }

  .headline {
    position: absolute; left: 0; top: 1050px; width: 1200px; text-align: center;
    font-family: var(--heading-font); font-weight: 400; color: var(--text-light);
    font-size: 54px; line-height: 72px; letter-spacing: 3px;
  }
  .tagline {
    position: absolute; left: 0; top: 1286px; width: 1200px; text-align: center;
    font-family: var(--body-font); font-style: italic; font-weight: 500;
    color: var(--gold-soft); font-size: 42px; letter-spacing: 2px;
  }

  .details-rule-v { position: absolute; left: 356px; top: 1384px; width: 2px; height: 640px; background: var(--gold); }
  .details-rule-h { position: absolute; left: 356px; top: 1626px; width: 694px; height: 2px; background: var(--gold); }

  .details {
    position: absolute; left: 398px; font-family: var(--body-font); font-weight: 600;
    color: var(--text-light); font-size: 30px; line-height: 50px;
  }
  .details em { font-style: italic; font-weight: 500; }
  .event-facts { top: 1384px; }
  .event-info { top: 1670px; }

  .partner-band { position: absolute; left: 0; top: 2090px; width: 1200px; height: 36px; background: var(--gold-band); }
  .partner-band .band-left {
    position: absolute; left: 0; top: 0; width: 340px; height: 36px; background: var(--grey-band);
    clip-path: polygon(0 0, 310px 0, 340px 100%, 0 100%);
  }
  .band-label {
    position: absolute; top: 0; line-height: 36px; font-family: var(--body-font); font-weight: 600;
    font-size: 19px; letter-spacing: 2px; color: var(--paper); text-transform: uppercase;
  }
  .band-label.partner { left: 108px; }
  .band-label.support { left: 712px; }

  .sponsors { position: absolute; left: 0; top: 2126px; width: 1200px; height: 274px; background: var(--paper); }
  .sponsor-name {
    position: absolute; font-family: var(--body-font); font-weight: 600; color: var(--logo-ink);
    display: flex; align-items: center; gap: 14px;
  }
  .sponsor-name.event-partner { left: 90px; top: 110px; font-size: 48px; }
  .sponsor-name.charity { left: 836px; top: 96px; font-size: 34px; line-height: 1.1; }
  .sponsor-name.charity .circle { width: 74px; height: 74px; border-radius: 50%; background: var(--badge-green); flex: none; }
  .partner-badge { position: absolute; left: 438px; top: 72px; width: 320px; height: 150px; border-radius: 10px; background: var(--badge-green); }
</style>
</head>
<body>
<main class="poster">
  <div class="hero-image" role="img" aria-label="Close-up photograph of a gold glitter masquerade mask with black feathers on a black background"></div>

  <div class="org-mark">
    <span class="mark-square"></span>
    <span class="mark-name">KEYSTONE INSTITUTE<br>Bright Builders WA</span>
  </div>

  <h1 class="headline">Join us in celebrating<br>the Annual Bright Builders<br>of Western Australia Gala</h1>
  <p class="tagline">with a night of dinner and entertainment.</p>

  <div class="details-rule-v"></div>
  <div class="details-rule-h"></div>

  <div class="details event-facts">
    Saturday July 13th, 2013<br>
    <em>Time:</em> 7pm Arrival<br>
    <em>Venue:</em> Corvane Ridgeway Hotel, Perth<br>
    <em>Dress:</em> Formal
  </div>

  <div class="details event-info">
    <em>The evening will include drinks,</em><br>
    <em>a three-course dinner, music and dancing.</em><br>
    Ticket price $139, on sale now!<br>
    To purchase tickets go to:<br>
    (website to be announced)<br>
    <em>Proceeds go to Makers Across Oceans</em><br>
    This is an 18+ event. Open to general public.
  </div>

  <div class="partner-band">
    <div class="band-left"></div>
    <span class="band-label partner">Event Partner</span>
    <span class="band-label support">In Support Of</span>
  </div>

  <section class="sponsors">
    <div class="sponsor-name event-partner">Tessaline</div>
    <div class="partner-badge"></div>
    <div class="sponsor-name charity"><span class="circle"></span><span>Makers<br>Across Oceans</span></div>
  </section>
</main>
</body>
</html>
```